Flyer for our prophetic church event

I need a flyer designed for the launching of our "7 Kindled Sabbath Gatherings" event. This event should high light the next 7 Sundays starting on February the 11th, 2018

Event Name:
7 Kindled Sabbaths

Event Slogan or topic:
Go and tell John ... the blind see, the lame walk, the lepers are cleansed, the deaf hear, the dead are raised,
the poor have the gospel preached to them.

Speaker:
Prophet Tobias Mwale

February 11th
February 18th
February 25th
March 4th
March 11th
March 18th
March 25th

Location:
Halvorn Community Center
583 Quillby Street
Portland, ME 04387
United States

Time:
10:00AM - 12:00PM

We welcome you all in the name of Jesus Christ

Contact Info:
Tel:+1(207) 555 0148 - Email:contact@brightvale-fellowship.org - Website: http://olvek.org

Target Market(s)

Young adults

Industry/Entity Type

Church

Font styles to use
Other font styles liked:
• Surprise me, I trust the designers skills

Colors

Designer to choose colors to be used in the design.

Requirements
Must have
• The Olvek logo
• Tobias Mwale's picture
• The
Should not have
• The background of the Tobias Mwale's picture

```html
<!DOCTYPE html>
<html lang="en">
<head>
<meta charset="utf-8">
<title>7 Kindled Sabbath Gatherings</title>
<link rel="stylesheet" href="https://fonts.googleapis.com/css2?family=Yellowtail&family=Dancing+Script:wght@700&family=Cinzel:wght@600;700&family=Lato:wght@400;700&family=Tinos:wght@400;700&display=swap">
<style>
  :root {
    --navy: #0f2f5a;
    --navy-deep: #0b2547;
    --gold: #e8b923;
    --gold-light: #f6d84a;
    --orange: #f2961c;
    --grey-band: #dcdcdc;
    --white: #ffffff;
    --ink: #1b1b1b;
    --sky-top: #2f4a75;
    --sky-mid: #b86a5a;
    --sky-low: #ec7a32;
    --glow: #ffb347;
    --cloth: #3b2a55;
  }
  * { margin: 0; padding: 0; box-sizing: border-box; }
  html, body { width: 806px; height: 1200px; overflow: hidden; background: var(--white); }
  .flyer { position: relative; width: 806px; height: 1200px; overflow: hidden; background: var(--white); font-family: "Lato", sans-serif; color: var(--ink); }

  .hero-art { position: absolute; left: 0; top: 0; width: 806px; height: 706px;
    background:
      radial-gradient(ellipse 260px 200px at 430px 380px, rgba(255,190,90,0.75) 0%, rgba(255,150,60,0.35) 55%, rgba(255,150,60,0) 100%),
      radial-gradient(ellipse 220px 120px at 80px 330px, rgba(255,170,70,0.55) 0%, rgba(255,170,70,0) 100%),
      radial-gradient(ellipse 200px 110px at 720px 470px, rgba(255,140,60,0.5) 0%, rgba(255,140,60,0) 100%),
      radial-gradient(ellipse 170px 150px at 390px 360px, rgba(70,40,80,0.35) 0%, rgba(70,40,80,0) 100%),
      radial-gradient(ellipse 260px 90px at 200px 200px, rgba(190,110,110,0.45) 0%, rgba(190,110,110,0) 100%),
      radial-gradient(ellipse 300px 100px at 640px 230px, rgba(160,100,120,0.4) 0%, rgba(160,100,120,0) 100%),
      linear-gradient(180deg, var(--sky-top) 0%, #5a5f80 18%, #9a6a72 36%, var(--sky-mid) 48%, var(--sky-low) 68%, #e0652a 85%, #c9552a 100%); }

  .brand { position: absolute; top: 72px; left: 0; width: 806px; text-align: center;
    font-family: "Tinos", serif; font-size: 56px; font-weight: 400; color: var(--white); letter-spacing: 1px; }

  .title-band { position: absolute; left: 0; top: 589px; width: 806px; height: 95px;
    background: linear-gradient(90deg, rgba(15,47,90,0) 0%, rgba(15,47,90,0.95) 14%, var(--navy) 50%, rgba(15,47,90,0.95) 86%, rgba(15,47,90,0) 100%);
    display: flex; align-items: center; justify-content: center; }
  .event-title { font-family: "Yellowtail", "Dancing Script", cursive; font-size: 50px; color: var(--white); font-weight: 400; white-space: nowrap; }

  .welcome-band { position: absolute; left: 0; top: 706px; width: 806px; height: 45px;
    background: linear-gradient(90deg, #c99a14 0%, var(--gold-light) 45%, var(--gold) 70%, #c99a14 100%);
    display: flex; align-items: center; justify-content: center;
    font-family: "Cinzel", serif; font-weight: 700; font-size: 22px; color: var(--navy); letter-spacing: 1px; }

  .scripture { position: absolute; right: 36px; top: 762px; width: 700px; text-align: right; }
  .scripture-lead { font-family: "Yellowtail", "Dancing Script", cursive; font-size: 42px; color: var(--navy); line-height: 1; }
  .scripture-text { margin-top: 12px; font-size: 14px; font-weight: 700; line-height: 21px; color: var(--ink); }

  .dates-band { position: absolute; left: 200px; top: 879px; width: 606px; height: 110px; background: var(--grey-band); }
  .date { position: absolute; font-weight: 700; white-space: nowrap; }
  .date sup { font-size: 0.6em; }
  .date.major { font-size: 21px; top: 20px; }
  .date.minor { font-size: 16px; top: 66px; }

  .event-time { position: absolute; left: 320px; top: 1008px; display: flex; gap: 10px; }
  .event-time .when { font-family: "Tinos", serif; font-size: 27px; line-height: 32px; color: var(--ink); }
  .venue { position: absolute; left: 492px; top: 1004px; display: flex; gap: 10px; }
  .venue-text { font-family: "Tinos", serif; font-size: 16px; line-height: 22px; color: var(--ink); }
  .venue-name { font-variant: small-caps; font-size: 19px; letter-spacing: 0.5px; }
  .icon { flex: none; margin-top: 6px; }

  .footer { position: absolute; left: 0; top: 1089px; width: 806px; height: 111px; background: var(--navy); }
  .contact-heading { position: absolute; left: 278px; top: 22px; font-family: "Tinos", serif; font-variant: small-caps;
    font-size: 18px; color: var(--white); text-decoration: underline; letter-spacing: 0.5px; }
  .contact-row { position: absolute; left: 278px; right: 24px; top: 58px; display: flex; justify-content: space-between; align-items: center;
    font-family: "Tinos", serif; font-weight: 700; color: var(--white); }
  .contact-item { display: flex; align-items: center; gap: 6px; white-space: nowrap; }
  .contact-item.phone { font-size: 16px; }
  .contact-item.small { font-size: 12.5px; }

  .speaker { position: absolute; left: 17px; top: 873px; width: 280px; height: 290px; }
  .speaker svg { position: absolute; left: 0; top: 0; }
  .speaker-caption { position: absolute; left: 0; width: 280px; top: 212px; text-align: center; font-family: "Tinos", serif; color: var(--navy-deep); }
  .speaker-role { font-variant: small-caps; font-size: 13px; line-height: 14px; }
  .speaker-name { font-variant: small-caps; font-size: 18px; line-height: 22px; letter-spacing: 0.5px; }
</style>
</head>
<body>
<main class="flyer">
  <div class="hero-art" role="img" aria-label="Glowing sunset sky behind a wooden cross draped in purple cloth"></div>
  <div class="brand">OLVEK</div>

  <div class="title-band"><h1 class="event-title">7 Kindled Sabbath Gatherings</h1></div>

  <div class="welcome-band">We welcome you all in the name of Jesus Christ</div>

  <section class="scripture">
    <p class="scripture-lead">Go and tell John ...</p>
    <p class="scripture-text">the blind see, the lame walk, the lepers are cleansed, the deaf hear, the dead are raised, the<br>poor have the gospel preached to them.</p>
  </section>

  <section class="dates-band">
    <span class="date major" style="left:101px">February 11<sup>th</sup></span>
    <span class="date major" style="left:267px">February 18<sup>th</sup></span>
    <span class="date major" style="left:433px">February 25<sup>th</sup></span>
    <span class="date minor" style="left:101px">March 4<sup>th</sup></span>
    <span class="date minor" style="left:223px">March 11<sup>th</sup></span>
    <span class="date minor" style="left:351px">March 18<sup>th</sup></span>
    <span class="date minor" style="left:479px">March 25<sup>th</sup></span>
  </section>

  <div class="event-time">
    <svg class="icon" width="18" height="18" viewBox="0 0 18 18" aria-hidden="true">
      <circle cx="9" cy="9" r="9" fill="var(--orange)"/>
      <path d="M9 4v5h4" stroke="#fff" stroke-width="2" fill="none" stroke-linecap="round"/>
    </svg>
    <div class="when">10:00AM-<br>12:00PM</div>
  </div>

  <div class="venue">
    <svg class="icon" width="14" height="19" viewBox="0 0 14 19" aria-hidden="true">
      <path d="M7 0C3 0 0 3 0 7c0 5 7 12 7 12s7-7 7-12c0-4-3-7-7-7z" fill="var(--orange)"/>
      <circle cx="7" cy="7" r="2.6" fill="#fff"/>
    </svg>
    <div class="venue-text">
      <div class="venue-name">Halvorn Community Center</div>
      <div>583 Quillby Street, Portland</div>
      <div>ME 04387 United States</div>
    </div>
  </div>

  <footer class="footer">
    <div class="contact-heading">Contact Us:</div>
    <div class="contact-row">
      <span class="contact-item phone">
        <svg width="14" height="14" viewBox="0 0 14 14" aria-hidden="true"><circle cx="7" cy="7" r="6" fill="none" stroke="var(--orange)" stroke-width="1.5"/><path d="M4.5 4c0 3 2.5 5.5 5.5 5.5l0.5-1.5-1.8-0.8-0.7 0.8c-1-0.4-1.9-1.3-2.3-2.3l0.8-0.7L5.7 3.3z" fill="var(--orange)"/></svg>
        +1(207) 555 0148
      </span>
      <span class="contact-item small">
        <svg width="13" height="10" viewBox="0 0 13 10" aria-hidden="true"><rect width="13" height="10" rx="1" fill="var(--orange)"/><path d="M1 1l5.5 4.5L12 1" stroke="var(--navy)" stroke-width="1.3" fill="none"/></svg>
        contact@brightvale-fellowship.org
      </span>
      <span class="contact-item small">
        <svg width="13" height="13" viewBox="0 0 13 13" aria-hidden="true"><g fill="none" stroke="var(--orange)" stroke-width="1.2"><circle cx="6.5" cy="6.5" r="5.8"/><ellipse cx="6.5" cy="6.5" rx="2.6" ry="5.8"/><path d="M0.7 6.5h11.6"/></g></svg>
        www.olvek.org
      </span>
    </div>
  </footer>

  <figure class="speaker">
    <svg width="280" height="290" viewBox="0 0 280 290">
      <defs>
        <clipPath id="speaker-disc"><circle cx="140" cy="143" r="132"/></clipPath>
        <linearGradient id="speaker-tone" x1="0" y1="0" x2="0" y2="1">
          <stop offset="0" stop-color="#d8cfc8"/>
          <stop offset="0.55" stop-color="#7a6a62"/>
          <stop offset="1" stop-color="#2a2a30"/>
        </linearGradient>
      </defs>
      <circle cx="140" cy="143" r="140" fill="var(--navy)"/>
      <circle cx="140" cy="143" r="136" fill="var(--white)"/>
      <g clip-path="url(#speaker-disc)">
        <rect x="0" y="0" width="280" height="290" fill="url(#speaker-tone)" role="img" aria-label="Portrait of speaker Prophet Tobias Mwale"/>
        <rect x="0" y="204" width="280" height="90" fill="var(--orange)"/>
      </g>
    </svg>
    <figcaption class="speaker-caption">
      <div class="speaker-role">Speaker:</div>
      <div class="speaker-role">Prophet</div>
      <div class="speaker-name">Tobias Mwale</div>
    </figcaption>
  </figure>
</main>
</body>
</html>
```